Coffeeshop menu for filter tip

We want to have a cannabis (coffeeshop) menu in the size 25mm wide x 60mm wide. Some examples attached.

it must have the following text:
Menu

WEED p/g
Oblivane €16
Cloudplum €14
Tide Runner €14
Quincefig €16
Mega Marsh €14
Grey Heron €14

HASH p/g
Tashar Amber €12
Pebble Frost€11
Lime Dunes €14
Ash Petal €10

Target Market(s)

tourist in Amsterdam

Requirements
Nice to have
• cannabis sign leaf
• No Cigarettes allowed symbol

```html
<!DOCTYPE html>
<html lang="en">
<head>
<meta charset="utf-8">
<title>Coffeeshop Menu</title>
<link rel="stylesheet" href="https://fonts.googleapis.com/css2?family=Jost:wght@300;400;500&display=swap">
<style>
  :root {
    --bg-top: #0b0b0b;
    --bg-bottom: #232523;
    --panel: #050505;
    --accent: #f2e31d;
    --white: #ffffff;
    --muted: #9a9a9a;
    --menu-grey: #cfcfcf;
    --leaf-tone: rgba(60, 66, 60, 0.35);
    --skyline: #0a0a0a;
  }
  * { margin: 0; padding: 0; box-sizing: border-box; }
  html, body { width: 1200px; height: 2880px; overflow: hidden; }
  body {
    position: relative;
    font-family: "Jost", sans-serif;
    background: linear-gradient(180deg, var(--bg-top) 0%, #151615 45%, var(--bg-bottom) 85%);
  }
  .leaf-backdrop {
    position: absolute; inset: 0;
    background:
      radial-gradient(ellipse 520px 640px at 1050px 1650px, var(--leaf-tone), transparent 70%),
      radial-gradient(ellipse 360px 520px at 80px 1200px, var(--leaf-tone), transparent 70%),
      radial-gradient(ellipse 320px 300px at 1000px 120px, var(--leaf-tone), transparent 70%);
  }
  .arc {
    position: absolute; left: -700px; top: 350px;
    width: 1900px; height: 1900px; border-radius: 50%;
    background: rgba(255,255,255,0.025);
  }
  .no-cig {
    position: absolute; left: 69px; top: 66px;
    display: flex; align-items: center; gap: 14px;
    color: var(--white); font-size: 38px; font-weight: 400; letter-spacing: 9px;
  }
  .section-title {
    position: absolute; color: var(--white);
    font-size: 108px; font-weight: 500; letter-spacing: 46px; line-height: 1;
  }
  .panel { position: absolute; background: var(--panel); }
  .unit {
    position: absolute; color: var(--muted); font-size: 44px; font-weight: 300;
  }
  .item {
    position: absolute; display: flex; align-items: center; justify-content: space-between;
    height: 80px;
  }
  .item-name {
    color: var(--accent); font-size: 50px; font-weight: 400; letter-spacing: 11px;
  }
  .item-price {
    color: var(--white); font-size: 64px; font-weight: 300; letter-spacing: -2px;
  }
  .weed-title { left: 420px; top: 268px; }
  .weed-tab { left: 896px; top: 296px; width: 213px; height: 100px; }
  .weed-panel { left: 349px; top: 389px; width: 760px; height: 827px; }
  .weed-unit { left: 982px; top: 346px; }
  .weed .item { left: 400px; width: 664px; }
  .hash-title { left: 145px; top: 1564px; }
  .hash-tab { left: 728px; top: 1589px; width: 181px; height: 100px; }
  .hash-panel { left: 80px; top: 1680px; width: 829px; height: 568px; }
  .hash-unit { left: 755px; top: 1630px; }
  .hash .item { left: 133px; width: 707px; }
  .skyline {
    position: absolute; left: 0; top: 2450px; width: 1200px; height: 206px;
    background: linear-gradient(180deg, transparent 0%, rgba(10,10,10,0.6) 40%, var(--skyline) 100%);
  }
  .footer {
    position: absolute; left: 0; top: 2656px; width: 1200px; height: 224px;
    background: #000; display: flex; align-items: center; justify-content: center;
  }
  .footer-title {
    color: var(--menu-grey); font-size: 160px; font-weight: 300;
    letter-spacing: 82px; margin-right: -82px; line-height: 1;
  }
</style>
</head>
<body>
  <div class="arc"></div>
  <div class="leaf-backdrop" role="img" aria-label="Faint cannabis leaf pattern in the background"></div>

  <div class="no-cig">
    <span>NO CIGARETTES</span>
    <svg width="46" height="46" viewBox="0 0 46 46" aria-hidden="true">
      <circle cx="23" cy="23" r="20" fill="none" stroke="#fff" stroke-width="3.5"/>
      <rect x="10" y="21" width="22" height="6" fill="none" stroke="#fff" stroke-width="2.5"/>
      <line x1="34" y1="21" x2="34" y2="27" stroke="#fff" stroke-width="2.5"/>
      <line x1="9" y1="9" x2="37" y2="37" stroke="#fff" stroke-width="3.5"/>
    </svg>
  </div>

  <section class="weed">
    <div class="panel weed-tab"></div>
    <div class="panel weed-panel"></div>
    <h2 class="section-title weed-title">WEED</h2>
    <span class="unit weed-unit">p/g</span>
    <div class="item" style="top:458px"><span class="item-name">OBLIVANE</span><span class="item-price">€16</span></div>
    <div class="item" style="top:582px"><span class="item-name">CLOUDPLUM</span><span class="item-price">€14</span></div>
    <div class="item" style="top:707px"><span class="item-name">TIDE RUNNER</span><span class="item-price">€14</span></div>
    <div class="item" style="top:834px"><span class="item-name">QUINCEFIG</span><span class="item-price">€16</span></div>
    <div class="item" style="top:958px"><span class="item-name">MEGA MARSH</span><span class="item-price">€14</span></div>
    <div class="item" style="top:1085px"><span class="item-name">GREY HERON</span><span class="item-price">€14</span></div>
  </section>

  <section class="hash">
    <div class="panel hash-tab"></div>
    <div class="panel hash-panel"></div>
    <h2 class="section-title hash-title">HASH</h2>
    <span class="unit hash-unit">p/g</span>
    <div class="item" style="top:1741px"><span class="item-name">TASHAR AMBER</span><span class="item-price">€12</span></div>
    <div class="item" style="top:1866px"><span class="item-name">PEBBLE FROST</span><span class="item-price">€11</span></div>
    <div class="item" style="top:1992px"><span class="item-name">LIME DUNES</span><span class="item-price">€14</span></div>
    <div class="item" style="top:2117px"><span class="item-name">ASH PETAL</span><span class="item-price">€10</span></div>
  </section>

  <div class="skyline" role="img" aria-label="Amsterdam city skyline silhouette"></div>

  <footer class="footer">
    <h1 class="footer-title">MENU</h1>
  </footer>
</body>
</html>
```